Stationary design for boutique production house

We need a stationary design for our production house, 'Lorno Productions' based in Singapore. We produce microfilms as well as podcasts, talkshows and events. Our logo is a stylized icon of our director, who is also the executive producer and host of our programs, Lorno. Our main company colors are Red, Black and white. We would like a clean, minimalist design incorporating our existing company logo that conveys a sense of urbanism and elegance.

Logo and font files are attached. f

Target Market(s)

We focus on lifestyle media rather than entertainment.

Industry/Entity Type

Boutique

Font styles to use
Serif
Sans Serif

Colors
ec1f27
ffffff
000000

Requirements
Must have
• Our company logo and at least one of our company colors.
Nice to have
• Our address and contact information.
Should not have
• Changes made to the company logo (using only certain parts of it is fine though)

```html
<!DOCTYPE html>
<html lang="en">
<head>
<meta charset="utf-8">
<title>Lorno Productions – Business Cards</title>
<link rel="stylesheet" href="https://fonts.googleapis.com/css2?family=Libre+Bodoni:wght@500&family=Jost:wght@400&display=swap">
<style>
  :root {
    --stage: #3b3b3b;
    --paper: #ffffff;
    --ink: #231f20;
    --red: #ec1f27;
    --muted: #9a9a9a;
    --faint: #ececec;
    --card-w: 320px;
    --card-h: 560px;
  }
  * { margin: 0; padding: 0; box-sizing: border-box; }
  html, body { width: 1200px; height: 659px; overflow: hidden; }
  body {
    background: var(--stage);
    display: flex;
    align-items: center;
    justify-content: center;
    gap: 60px;
    font-family: "Jost", "Helvetica Neue", Arial, sans-serif;
  }
  .card {
    position: relative;
    width: var(--card-w);
    height: var(--card-h);
    background: var(--paper);
    overflow: hidden;
    box-shadow: 0 10px 24px rgba(0,0,0,.35);
  }
  .card__shape { position: absolute; inset: 0; width: 100%; height: 100%; }

  .wordmark {
    position: absolute;
    font-family: "Libre Bodoni", "Bodoni Moda", Georgia, serif;
    font-weight: 500;
    color: var(--ink);
    text-align: center;
    line-height: 1.05;
    letter-spacing: .02em;
  }

  /* Front */
  .brand-mark {
    position: absolute;
    top: 82px;
    left: 188px;
    width: 84px;
    height: 84px;
    border-radius: 50%;
    background: var(--ink);
  }
  .card--front .wordmark { top: 178px; left: 140px; width: 180px; font-size: 20px; }
  .card--front .wordmark__rule {
    display: block;
    height: 1px;
    margin: 6px 14px 0;
    background: var(--muted);
  }

  .contact {
    position: absolute;
    left: 26px;
    bottom: 40px;
    color: var(--paper);
    font-size: 13px;
    line-height: 1.45;
  }
  .contact__name { font-size: 19px; letter-spacing: .04em; }
  .contact__role { font-size: 14px; letter-spacing: .04em; margin-bottom: 14px; }
  .contact__address { margin-bottom: 8px; }
  .contact__list { list-style: none; }
  .contact__list li { display: flex; align-items: center; gap: 8px; }
  .contact__icon { width: 11px; height: 11px; fill: var(--paper); flex: none; }

  /* Back */
  .watermark {
    position: absolute;
    top: 300px;
    left: 30px;
    width: 320px;
    height: 320px;
    border-radius: 50%;
    background: var(--faint);
  }
  .card--back .wordmark { top: 72px; left: 0; right: 0; font-size: 27px; }
  .wordmark__dot {
    display: inline-block;
    width: 9px; height: 9px;
    border-radius: 50%;
    background: var(--red);
    margin-bottom: 6px;
  }
  .card--back .rule {
    position: absolute;
    top: 158px; left: 66px; right: 66px;
    height: 1px; background: var(--muted);
  }
  .card--back .web {
    position: absolute;
    top: 166px; left: 0; right: 0;
    text-align: center;
    font-size: 11px;
    letter-spacing: .2em;
    color: #555;
  }
</style>
</head>
<body>

  <section class="card card--front">
    <svg class="card__shape" viewBox="0 0 320 560" preserveAspectRatio="none" aria-hidden="true">
      <path d="M64,0 C80,215 185,350 320,392 L320,560 L0,560 L0,0 Z" fill="var(--red)"/>
      <path d="M54,0 C68,232 178,372 320,416 L320,560 L0,560 L0,0 Z" fill="var(--ink)"/>
    </svg>

    <div class="brand-mark" role="img" aria-label="Company logo placement"></div>
    <div class="wordmark">LORNO<br>PRODUCTIONS<span class="wordmark__rule"></span></div>

    <div class="contact">
      <p class="contact__name">MAREN HOLT</p>
      <p class="contact__role">CEO/FOUNDER</p>
      <p class="contact__address">42 Kestrel Row<br>Tanjong Quay 208114</p>
      <ul class="contact__list">
        <li><svg class="contact__icon" viewBox="0 0 12 12"><path d="M2.5 0.5 L4.5 0.5 L5.3 3.2 L3.9 4.3 C4.6 5.8 6.2 7.4 7.7 8.1 L8.8 6.7 L11.5 7.5 L11.5 9.5 C11.5 10.6 10.6 11.5 9.5 11.5 C4.5 11.2 0.8 7.5 0.5 2.5 C0.5 1.4 1.4 0.5 2.5 0.5 Z"/></svg>614 205 7731</li>
        <li><svg class="contact__icon" viewBox="0 0 12 12"><path d="M3 0 H9 A1 1 0 0 1 10 1 V11 A1 1 0 0 1 9 12 H3 A1 1 0 0 1 2 11 V1 A1 1 0 0 1 3 0 Z M3.2 1.5 V9.5 H8.8 V1.5 Z"/></svg>652 318 0496</li>
        <li><svg class="contact__icon" viewBox="0 0 12 12"><path d="M3 0 H9 V4 H11 A1 1 0 0 1 12 5 V10 A1 1 0 0 1 11 11 H1 A1 1 0 0 1 0 10 V5 A1 1 0 0 1 1 4 H3 Z M4 1 V5 H8 V1 Z"/></svg>627 540 1183</li>
        <li><svg class="contact__icon" viewBox="0 0 12 12"><path d="M0 2 H12 V10 H0 Z M1 3 L6 6.6 L11 3 V3 Z" fill-rule="evenodd"/></svg>hello@lornostudio.com</li>
        <li><svg class="contact__icon" viewBox="0 0 12 12"><circle cx="6" cy="6" r="5.5"/><path d="M0.5 6 H11.5 M6 0.5 C3 3.5 3 8.5 6 11.5 M6 0.5 C9 3.5 9 8.5 6 11.5" stroke="var(--ink)" stroke-width="0.9" fill="none"/></svg>www.lornostudio.com</li>
      </ul>
    </div>
  </section>

  <section class="card card--back">
    <div class="watermark" role="img" aria-label="Faint enlarged company logo decoration"></div>
    <div class="wordmark"><span class="wordmark__dot"></span><br>LORNO<br>PRODUCTIONS</div>
    <div class="rule"></div>
    <p class="web">www.lornostudio.com</p>
  </section>

</body>
</html>
```